Post storm repair flyer

looking for an eye catching 6x9 postcard to send out to single family home owners advertising a "Post Storm Repair Special" explaining that after the recent hurricanes its very important to have your roof checked and any repairs fixed right away before they become a bigger more costly problem and that even though your home wasn't directly hit by the storm the high wind gust could've cause unseen damage.
offer $200 off any repair *some rules may apply
Crest Roofing
877.512.DUNE
www.DuneRoofingco.example

```html
<!DOCTYPE html>
<html lang="en">
<head>
<meta charset="utf-8">
<title>Post-Storm Roof Repair Special – Crest Roofing</title>
<link href="https://fonts.googleapis.com/css2?family=Montserrat:wght@400;500;600;700;800;900&display=swap" rel="stylesheet">
<style>
:root{
  --bg:#d4d5d7;
  --gold:#e8ae22;
  --black:#000000;
  --white:#ffffff;
  --ink:#111111;
  --rule:#555555;
  --sky-dark:#2a2e33;
  --sky-mid:#5a6068;
  --roof:#6b5a52;
}
*{box-sizing:border-box;margin:0;padding:0}
html,body{width:1200px;height:918px;overflow:hidden;background:var(--bg);font-family:'Montserrat',sans-serif}
.postcard{position:absolute;top:146px;width:415px;height:623px;overflow:hidden}
.front{left:164px;background:var(--black)}
.back{left:621px;background:var(--white)}

/* front */
.hero-photo{position:absolute;left:0;top:0;width:415px;height:358px;
  background:linear-gradient(160deg,var(--sky-dark) 0%,var(--sky-mid) 45%,#4a4f55 62%,var(--roof) 100%)}
.headline{position:absolute;left:24px;top:22px;font-weight:800;font-size:38px;line-height:34px;color:var(--white);letter-spacing:.2px}
.headline .accent{color:var(--gold)}
.headline-rule{position:absolute;left:0;top:134px;width:212px;height:3px;background:var(--gold)}
.intro{position:absolute;left:24px;top:143px;width:205px;font-size:11.6px;line-height:14px;color:var(--white);font-weight:500}
.front-brand{position:absolute;left:24px;top:322px;font-size:14px;font-weight:500;color:var(--gold);letter-spacing:.3px}
.offer-badge{position:absolute;left:191px;top:177px;width:197px;height:197px;border-radius:50%;background:var(--gold);
  display:flex;flex-direction:column;align-items:center;justify-content:center;color:var(--black);transform:rotate(-10deg)}
.offer-badge .amount{font-weight:800;font-size:56px;line-height:48px}
.offer-badge .off{font-weight:800;font-size:58px;line-height:50px}
.offer-badge .scope{font-weight:700;font-size:21px;line-height:24px;margin-left:30px}
.promise-band{position:absolute;left:0;top:358px;width:415px;height:92px;background:var(--black);padding:23px 33px 0;
  color:var(--white);font-size:13.6px;line-height:16.5px;font-weight:500}
.promise-band strong,.back-promise strong{color:var(--gold);font-weight:800;font-size:16px}
.terms-band{position:absolute;left:0;top:450px;width:415px;height:87px;
  background:linear-gradient(100deg,#ececec 0%,#dcdcdc 55%,#efefef 100%);
  text-align:center;padding-top:24px;font-size:14.6px;line-height:18.5px;font-weight:500;color:var(--ink);letter-spacing:.3px}
.terms-band .accent{color:var(--gold);font-weight:800}
.contact-band{position:absolute;left:0;top:537px;width:415px;height:86px;background:var(--gold);
  display:flex;align-items:center;padding-left:34px;gap:14px}
.brand-name{font-weight:700;font-size:12px;line-height:14px;width:46px}
.contact-band .brand-name{color:var(--black)}
.contact-text{text-align:center}
.phone{font-weight:800;font-size:34px;line-height:36px;letter-spacing:-.5px}
.web{font-weight:800;font-size:10.5px;letter-spacing:1.1px}
.contact-band .phone,.contact-band .web{color:var(--black)}

/* back */
.back-headline{position:absolute;left:0;top:26px;width:415px;text-align:center;font-weight:800;font-size:27px;line-height:24px;color:var(--black)}
.back-promise{position:absolute;left:40px;top:83px;width:335px;text-align:center;font-size:13.4px;line-height:16.5px;font-weight:500;color:var(--ink)}
.back-band{position:absolute;left:0;top:151px;width:415px;height:94px;background:var(--black);
  display:flex;align-items:center;padding-left:38px;gap:14px}
.back-band .brand-name{color:var(--gold)}
.back-band .phone{color:var(--gold)}
.back-band .web{color:var(--white);margin-top:4px}
.stamp-box{position:absolute;left:282px;top:295px;width:105px;height:116px;border:1px solid var(--rule)}
.address-line{position:absolute;left:38px;width:220px;height:1px;background:var(--rule)}
</style>
</head>
<body>

<section class="postcard front">
  <div class="hero-photo" role="img" aria-label="Palm trees bending in hurricane wind above a storm-damaged shingle roof"></div>
  <h1 class="headline">POST-STORM<br><span class="accent">ROOF REPAIR</span><br>SPECIAL!</h1>
  <div class="headline-rule"></div>
  <p class="intro">Recent storms can cause hidden damage to your roof. Don't wait until it's too late—get a professional inspection today!</p>
  <div class="front-brand">Crest Roofing</div>
  <div class="offer-badge">
    <span class="amount">$200</span>
    <span class="off">OFF</span>
    <span class="scope">Any Repair</span>
  </div>
  <div class="promise-band"><strong>PROTECT YOUR HOME</strong> and avoid costly repairs by addressing storm damage early. Our expert team is ready to help!</div>
  <div class="terms-band">OFFER INCLUDES A FREE INSPECTION AND<br><span class="accent">$200 OFF</span> ANY QUALIFYING REPAIR.*</div>
  <div class="contact-band">
    <div class="brand-name">Crest Roofing</div>
    <div class="contact-text">
      <div class="phone">877.512.DUNE</div>
      <div class="web">www.DuneRoofingco.example</div>
    </div>
  </div>
</section>

<section class="postcard back">
  <h2 class="back-headline">POST-STORM<br>ROOF REPAIR SPECIAL!</h2>
  <p class="back-promise"><strong>PROTECT YOUR HOME</strong> and avoid costly repairs by addressing storm damage early. Our expert team is ready to help!</p>
  <div class="back-band">
    <div class="brand-name">Crest Roofing</div>
    <div class="contact-text">
      <div class="phone">877.512.DUNE</div>
      <div class="web">www.DuneRoofingco.example</div>
    </div>
  </div>
  <div class="stamp-box"></div>
  <div class="address-line" style="top:452px"></div>
  <div class="address-line" style="top:489px"></div>
  <div class="address-line" style="top:526px"></div>
  <div class="address-line" style="top:563px"></div>
</section>

</body>
</html>
```